Whitcombe Business Card Design

The name of the business is Dario Whitcombe, CPA LLC
The service that we offer is Accounting, Tax & Consulting Services. I need it to have the following items:
Dario Whitcombe, Principal
Phone Number
Email Address
Physical Address

I have attached the company logo, one in black and one in white. Please provide a design in black background and the other in white background. Please include "Accounting, Tax & Consulting Services". I want the business card to be clean and very professional.

```html
<!DOCTYPE html>
<html lang="en">
<head>
<meta charset="utf-8">
<title>Dario Whitcombe, CPA LLC – Business Card</title>
<link href="https://fonts.googleapis.com/css2?family=Montserrat:wght@400;500;600;700&display=swap" rel="stylesheet">
<style>
  :root {
    --page-bg: #141414;
    --card-bg: #222223;
    --brand-red: #9b1c20;
    --logo-grey: #4e4e50;
    --tagline-grey: #7a7a7c;
    --text-light: #f2f2f2;
  }
  * { margin: 0; padding: 0; box-sizing: border-box; }
  html, body {
    width: 1200px; height: 927px; overflow: hidden;
    background: var(--page-bg);
    font-family: "Montserrat", Arial, sans-serif;
  }
  .sheet {
    width: 1200px; height: 927px;
    display: flex; flex-direction: column;
    align-items: center; justify-content: center; gap: 40px;
  }
  .card {
    position: relative;
    width: 700px; height: 400px;
    background: var(--card-bg);
    border-radius: 26px;
    overflow: hidden;
    box-shadow: 0 14px 30px rgba(0,0,0,.55);
  }

  /* Front */
  .card--front .brand {
    position: absolute; left: 150px; top: 140px;
  }
  .brand__name {
    display: flex; align-items: center; gap: 14px;
    font-size: 30px; font-weight: 500; letter-spacing: 1px;
    color: var(--logo-grey); text-transform: uppercase;
  }
  .brand__square {
    width: 22px; height: 22px; background: var(--brand-red);
  }
  .brand__title {
    margin-top: 6px; margin-left: 36px;
    font-size: 22px; font-weight: 600; letter-spacing: 4px;
    color: var(--tagline-grey); text-transform: uppercase;
  }
  .brand__services {
    margin-top: 22px; margin-left: 36px;
    font-size: 17px; font-weight: 700; letter-spacing: .5px;
    color: var(--tagline-grey);
  }

  /* Back */
  .name-band {
    position: absolute; left: 330px; top: 76px;
    width: 370px; height: 56px;
    background: var(--brand-red);
    display: flex; align-items: center; padding-left: 22px;
    color: var(--text-light);
    font-size: 19px; font-weight: 700; letter-spacing: .5px;
    text-transform: uppercase;
  }
  .contact {
    position: absolute; left: 352px; top: 162px;
    list-style: none; color: var(--text-light);
    font-size: 15px; font-weight: 400;
  }
  .contact__item {
    display: flex; align-items: center; gap: 14px;
    margin-bottom: 16px; line-height: 1.4;
  }
  .contact__icon {
    flex: 0 0 26px; width: 26px; height: 26px;
  }
  .card--back .brand {
    position: absolute; left: 46px; top: 250px;
  }
  .card--back .brand__name { font-size: 17px; gap: 9px; }
  .card--back .brand__square { width: 13px; height: 13px; }
  .card--back .brand__title {
    font-size: 12px; letter-spacing: 2.5px; margin-left: 22px; margin-top: 4px;
  }
</style>
</head>
<body>
<main class="sheet">

  <section class="card card--front">
    <div class="brand">
      <div class="brand__name"><span class="brand__square"></span>Dario Whitcombe, CPA LLC</div>
      <div class="brand__title">Certified Public Accountant</div>
      <div class="brand__services">Accounting, Tax &amp; Consulting Services</div>
    </div>
  </section>

  <section class="card card--back">
    <div class="name-band">Dario Whitcombe, Principal</div>

    <ul class="contact">
      <li class="contact__item">
        <svg class="contact__icon" viewBox="0 0 26 26" aria-hidden="true">
          <circle cx="13" cy="13" r="13" fill="var(--brand-red)"/>
          <path d="M13 6a5 5 0 0 0-5 5c0 3.6 5 9 5 9s5-5.4 5-9a5 5 0 0 0-5-5z" fill="#fff"/>
          <circle cx="13" cy="11" r="2" fill="var(--brand-red)"/>
        </svg>
        <span>#27-C, Larkfield Court,<br>Orchard Lane, Brookhaven, 410238</span>
      </li>
      <li class="contact__item">
        <svg class="contact__icon" viewBox="0 0 26 26" aria-hidden="true">
          <circle cx="13" cy="13" r="13" fill="var(--brand-red)"/>
          <path d="M7 11c0-2 3-3.5 6-3.5s6 1.5 6 3.5l-2.2.8-.8-1.8h-6l-.8 1.8zM8.5 13h9l1 5h-11z" fill="#fff"/>
        </svg>
        <span>555-204-7391</span>
      </li>
      <li class="contact__item">
        <svg class="contact__icon" viewBox="0 0 26 26" aria-hidden="true">
          <circle cx="13" cy="13" r="13" fill="var(--brand-red)"/>
          <rect x="6.5" y="8.5" width="13" height="9" fill="#fff"/>
          <path d="M6.5 8.5 13 14l6.5-5.5" fill="none" stroke="var(--brand-red)" stroke-width="1.3"/>
        </svg>
        <span>info@dariowhitcombecpa.com</span>
      </li>
      <li class="contact__item">
        <svg class="contact__icon" viewBox="0 0 26 26" aria-hidden="true">
          <circle cx="13" cy="13" r="13" fill="var(--brand-red)"/>
          <circle cx="13" cy="13" r="6.5" fill="none" stroke="#fff" stroke-width="1.5"/>
          <path d="M6.5 13h13M13 6.5c-3 3.5-3 9.5 0 13M13 6.5c3 3.5 3 9.5 0 13" fill="none" stroke="#fff" stroke-width="1.2"/>
        </svg>
        <span>www.dariowhitcombecpa.com</span>
      </li>
    </ul>

    <div class="brand">
      <div class="brand__name"><span class="brand__square"></span>Dario Whitcombe, CPA LLC</div>
      <div class="brand__title">Certified Public Accountant</div>
    </div>
  </section>

</main>
</body>
</html>
```